GlassHaven Artbook for Okanagan Region, British Columbia

Creating an art book: GlassHaven, for the Okanagan Wine Region in British Columbia, Canada. Would like smart, modern, clean and linear...cool, sexy urban, not ugly boring suburban... I need a cover that appeals to the wino in all of us! Title: GlassHaven -Marla Dovicki
Updates
Thank you all kindly for your efforts. I have added some files so that you can get a sense of my aesthetic...it's never easy trying to figure it out, is it? I will hopefully have dimensions of book soon...cheers, Marla
would anyone please design a giant wine bottle with the wine label that looks like a label but says glasshaven...just curious to see if it works as a design or not...thank you.
Target Market(s)
Designing this wine art book of quotes to wineries in Okanagan BC. Buyer is wine lover and tourist ready to spend his vacation bucks on this wonderful book!
Look and feel

```html
<!DOCTYPE html>
<html lang="en">
<head>
<meta charset="utf-8">
<title>GlassHaven – Cover</title>
<link rel="stylesheet" href="https://fonts.googleapis.com/css2?family=Source+Sans+3:wght@600&family=Mulish:wght@300&display=swap">
<style>
  :root {
    --page: #ffffff;
    --cover: #e4e4e2;
    --title: #ffffff;
    --wine-red: #ed1c24;
    --wine-red-soft: #f0383f;
    --author: #3f3f3f;
  }
  html, body {
    margin: 0;
    padding: 0;
    width: 1200px;
    height: 1000px;
    overflow: hidden;
    background: var(--page);
  }
  .canvas {
    position: relative;
    width: 1200px;
    height: 1000px;
  }
  .book-cover {
    position: absolute;
    left: 362px;
    top: 157px;
    width: 471px;
    height: 652px;
    background: var(--cover);
  }
  .bottle-artwork {
    position: absolute;
    left: 92px;
    top: 253px;
    width: 318px;
    height: 28px;
    background: linear-gradient(90deg, var(--wine-red), var(--wine-red-soft), var(--wine-red));
  }
  .book-title {
    position: absolute;
    z-index: 1;
    left: 0;
    width: 100%;
    top: 220px;
    margin: 0;
    text-align: center;
    font-family: "Source Sans 3", sans-serif;
    font-weight: 600;
    font-size: 37px;
    line-height: 1;
    letter-spacing: 3.5px;
    color: var(--title);
  }
  .book-author {
    position: absolute;
    left: 0;
    width: 100%;
    top: 562px;
    margin: 0;
    text-align: center;
    font-family: "Mulish", sans-serif;
    font-weight: 300;
    font-size: 15px;
    letter-spacing: 3px;
    color: var(--author);
  }
</style>
</head>
<body>
<div class="canvas">
  <section class="book-cover">
    <div class="bottle-artwork" role="img" aria-label="Illustration of three red wine bottles lying on their sides in a row"></div>
    <h1 class="book-title">GLASSHAVEN</h1>
    <p class="book-author">MARLA DOVICKI</p>
  </section>
</div>
</body>
</html>
```